Restyle corporate identity (+ logo) for a road construction company

We need a new logo and stationary design for our company VARNOK path. VARNOK path® increases the road base strength, while reducing major costs and time of road construction. Attached some examples of the current design.

Our wishes for the new logo:
- Business look
- Style sheet
- Modern

More information: www.varnokpath.example
Updates

Target Market(s)

Government

Industry/Entity Type

Construction

Requirements
Must have
• Logo (with road sign) + text

```html
<!DOCTYPE html>
<html lang="en">
<head>
<meta charset="utf-8">
<title>VARNOK path – Stationery</title>
<link rel="stylesheet" href="https://fonts.googleapis.com/css2?family=Open+Sans:wght@400;600;700&display=swap">
<style>
:root{
  --green:#9bc23c;
  --green-soft:#e4efd0;
  --grey:#6d6e70;
  --grey-light:#b4b5b7;
  --paper:#ffffff;
  --paper-env:#f3f3f3;
  --ink:#3a3a3a;
  --bg-top:#f2f2f2;
  --bg-bottom:#c9c9c9;
}
*{box-sizing:border-box;margin:0;padding:0}
html,body{width:1200px;height:1048px;overflow:hidden}
body{
  font-family:"Open Sans",Arial,sans-serif;
  background:radial-gradient(ellipse at 30% 30%,var(--bg-top) 0%,#e0e0e0 55%,var(--bg-bottom) 100%);
  position:relative;color:var(--ink);
}
.sheet{position:absolute;background:var(--paper);box-shadow:0 6px 18px rgba(0,0,0,.22);overflow:hidden}
.band{position:absolute;left:0;width:100%}
.wordmark{display:flex;align-items:center;gap:8px;font-weight:700;color:var(--grey);white-space:nowrap;letter-spacing:.5px}
.wordmark .mark{background:var(--green);flex:none}
.faint-square{position:absolute;background:var(--green-soft);opacity:.7}
.label{color:var(--green)}

/* letterhead */
.letterhead{left:60px;top:40px;width:440px;height:622px}
.letterhead .wordmark{position:absolute;left:150px;top:60px;font-size:26px}
.letterhead .wordmark .mark{width:18px;height:18px}
.letterhead .faint-square{left:280px;top:300px;width:110px;height:110px}
.letterhead .rule{position:absolute;left:24px;width:320px;top:500px;height:2px;background:var(--green)}
.letterhead .footer{position:absolute;left:40px;top:512px;width:310px;font-size:10px;font-weight:700;line-height:1.45}
.letterhead .address{margin-bottom:8px}
.letterhead .contacts{display:flex;gap:14px;font-size:9px;line-height:1.5}
.letterhead .contacts p{white-space:nowrap}
.letterhead .contacts .phones{padding-left:14px;border-left:1px solid var(--grey-light)}

/* envelope */
.envelope{left:420px;top:490px;width:720px;height:360px;background:var(--paper-env)}
.envelope .wordmark{position:absolute;left:100px;top:52px;font-size:30px}
.envelope .wordmark .mark{width:20px;height:20px}
.envelope .sender{position:absolute;left:60px;top:190px;font-size:11px;line-height:1.45}
.envelope .sender strong{font-weight:700;color:var(--grey)}
.envelope .faint-square{left:560px;top:180px;width:110px;height:110px}
.envelope .web{position:absolute;right:24px;bottom:42px;font-size:12px;color:var(--grey)}

/* cards */
.card{width:290px;height:166px}
.card-front{left:850px;top:110px}
.card-back{left:850px;top:298px}
.card-front .wordmark{position:absolute;left:90px;top:52px;font-size:22px}
.card .wordmark .mark{width:14px;height:14px}
.card-front .faint-square{left:12px;top:10px;width:46px;height:46px}
.card-front .web{position:absolute;left:14px;bottom:12px;font-size:8px;color:#fff}
.card-back .wordmark{position:absolute;left:16px;top:22px;font-size:18px}
.card-back .lines{position:absolute;left:12px;top:92px;font-size:6.5px;color:#fff;line-height:1.55}
.card-back .person{position:absolute;right:14px;bottom:12px;text-align:right;font-size:6px;color:var(--grey)}
.card-back .person b{display:block;font-size:8px;color:var(--ink)}
.card-back .faint-square{right:10px;top:80px;width:40px;height:40px}

/* logo sheet */
.logo-display{position:absolute;left:56px;top:880px}
.logo-display .wordmark{font-size:62px;gap:14px}
.logo-display .wordmark .mark{width:46px;height:46px}
.logo-display .underline{margin-top:8px;width:190px;height:2px;background:var(--grey)}
</style>
</head>
<body>

<section class="sheet letterhead" aria-label="Letterhead">
  <svg class="band" style="top:0" width="440" height="40" viewBox="0 0 440 40" aria-hidden="true">
    <polygon points="0,0 440,0 440,22 240,22 225,10 210,22 0,22" fill="var(--green)"/>
    <rect x="424" y="0" width="16" height="40" fill="var(--green)"/>
  </svg>
  <div class="wordmark"><span class="mark"></span>VARNOK path</div>
  <div class="faint-square"></div>
  <div class="rule"></div>
  <div class="footer">
    <p class="address">Address Line 1, Address Line2,<br>Address Line 3</p>
    <div class="contacts">
      <p><span class="label">Email -</span> mail@varnokpath.example<br><span class="label">WEB -</span> www.varnokpath.example</p>
      <p class="phones"><span class="label">Tel. -</span> +123 456 780<br><span class="label">Fax.-</span> +123 456 789</p>
    </div>
  </div>
  <svg class="band" style="bottom:0" width="440" height="24" viewBox="0 0 440 24" aria-hidden="true">
    <rect width="440" height="24" fill="var(--green)"/>
    <polygon points="250,0 440,0 440,24 262,24" fill="var(--grey-light)"/>
  </svg>
</section>

<section class="sheet envelope" aria-label="Envelope">
  <svg class="band" style="top:0" width="720" height="40" viewBox="0 0 720 40" aria-hidden="true">
    <polygon points="0,0 720,0 720,30 140,30 124,16 108,30 0,30" fill="var(--green)"/>
  </svg>
  <div class="wordmark"><span class="mark"></span>VARNOK path</div>
  <p class="sender"><strong>Address Line 1, Address Line2,<br>Address Line 3</strong><br>
    <span class="label">Email -</span> mail@varnokpath.example<br>
    <span class="label">Tel.&nbsp;&nbsp;-</span> +123 456 780<br>
    <span class="label">Fax.&nbsp;-</span> +123 456 789</p>
  <div class="faint-square"></div>
  <p class="web">www.varnokpath.example</p>
  <svg class="band" style="bottom:0" width="720" height="30" viewBox="0 0 720 30" aria-hidden="true">
    <polygon points="0,0 300,0 312,30 0,30" fill="var(--green)"/>
    <polygon points="300,0 720,0 720,30 312,30" fill="var(--grey-light)"/>
  </svg>
</section>

<section class="sheet card card-front" aria-label="Business card front">
  <div class="faint-square"></div>
  <div class="wordmark"><span class="mark"></span>VARNOK path</div>
  <svg class="band" style="bottom:0" width="290" height="34" viewBox="0 0 290 34" aria-hidden="true">
    <polygon points="0,0 120,0 132,34 0,34" fill="var(--green)"/>
    <polygon points="120,12 290,12 290,34 132,34" fill="var(--grey-light)"/>
  </svg>
  <p class="web">www.varnokpath.example</p>
</section>

<section class="sheet card card-back" aria-label="Business card back">
  <div class="wordmark"><span class="mark"></span>VARNOK path</div>
  <svg class="band" style="top:84px" width="290" height="82" viewBox="0 0 290 82" aria-hidden="true">
    <polygon points="0,0 150,0 164,60 0,60" fill="var(--green)"/>
    <polygon points="164,60 290,60 290,82 170,82" fill="var(--grey-light)"/>
  </svg>
  <p class="lines">+123 456 780<br>+123 456 789<br>mail@varnokpath.example<br>www.varnokpath.example</p>
  <div class="faint-square"></div>
  <p class="person"><b>YOUR NAME</b>Position<br>Address Line 1, Address Line 2</p>
</section>

<section class="logo-display" aria-label="Logo">
  <div class="wordmark"><span class="mark"></span>VARNOK path</div>
  <div class="underline"></div>
</section>

</body>
</html>
```